Webdesign für Personalvermittlung
Zielgruppe
Personalvermittlung
Aufgabenstellung
es soll einladend - nicht zu überladen und natürlich cool und modern sein

```html
<!DOCTYPE html>
<html lang="de">
<head>
<meta charset="utf-8">
<title>Pflegeplatz Job – Personalvermittlung</title>
<link rel="stylesheet" href="https://fonts.googleapis.com/css2?family=Inter:ital,wght@0,400;0,500;0,700;1,400&display=swap">
<style>
:root{
  --sky:#7ecbea;
  --azure:#29a9e1;
  --plum:#9c3a8d;
  --rose:#c9437f;
  --ink:#111;
  --card:#d9d9d9;
  --line:#cfcfcf;
  --white:#fff;
  --star:#f5b85a;
}
*{box-sizing:border-box;margin:0;padding:0}
html,body{width:1200px;height:3822px;overflow:hidden}
body{position:relative;font-family:"Inter",sans-serif;color:var(--ink);background:var(--white)}
.abs{position:absolute}
/* header */
.site-header{left:0;top:0;width:1200px;height:95px;background:var(--white)}
.brand{left:53px;top:30px;display:flex;align-items:center;gap:10px;font-weight:700;font-size:18px;color:var(--plum)}
.brand-square{width:26px;height:26px;background:var(--plum);border-radius:4px}
.main-nav{left:427px;top:34px;display:flex;gap:21px;font-size:20px}
.social{top:35px;width:24px;height:24px;border-radius:50%;background:var(--plum)}
/* hero */
.hero{left:0;top:95px;width:1200px;height:665px;background:var(--sky)}
.hero-title{left:52px;top:182px;font-size:42px;line-height:49px;font-weight:700;color:var(--white)}
.hero-sub{left:49px;top:370px;font-size:28px;line-height:33px;font-weight:700;color:var(--plum)}
.btn{display:flex;align-items:center;justify-content:center;border-radius:24px;font-size:21px}
.btn-solid{background:var(--plum);color:var(--white)}
.btn-outline{border:2px solid var(--rose);color:var(--rose);background:var(--white)}
.video{left:516px;top:178px;width:627px;height:359px;background:var(--white);border:2px solid #e4e4e4}
.video-name{left:0;width:100%;top:200px;text-align:center;font-size:15px;font-weight:700;color:#2a3b6b}
.video-bar{left:8px;right:8px;bottom:8px;height:18px;background:#7d7d7d;border-radius:4px}
.video-track{left:80px;right:70px;top:8px;height:3px;background:#bdbdbd}
.video-chip{left:8px;top:12px;width:48px;height:16px;background:#7d7d7d;border-radius:4px}
/* section heads */
.rule{height:3px;background:var(--plum)}
.section-title{font-size:27px;line-height:33px;font-weight:700}
.accent{color:var(--plum)}
/* feature cards */
.feature{width:258px;height:258px;border:3px solid var(--azure);border-radius:12px;background:var(--white);box-shadow:0 3px 4px rgba(0,0,0,.12);display:flex;flex-direction:column;align-items:center;justify-content:center;text-align:center;font-size:27px;line-height:33px;padding:0 16px}
.feature svg{margin-bottom:24px}
.feature-note{background:var(--azure);border-color:var(--azure);color:var(--white);font-size:16.5px;line-height:20px;padding:0 18px}
/* floating contact */
.fab{left:1114px;width:56px;height:56px;border-radius:50%;display:flex;align-items:center;justify-content:center}
/* testimonials */
.reviews{left:0;top:1707px;width:1200px;height:663px;background:var(--sky)}
.review{top:2005px;width:351px;height:220px;background:var(--card);border-radius:24px;padding:66px 24px 0 26px;font-size:17px;line-height:20px}
.avatar{top:1972px;width:68px;height:68px;border-radius:50%;background:radial-gradient(circle at 50% 40%,#c9a99a,#5a4a45);border:3px solid var(--white)}
.review-foot{margin-top:10px;border-top:3px solid var(--azure);padding-top:14px;display:flex;gap:16px;font-size:20px}
.stars{color:var(--star);letter-spacing:1px}
.stars .off{color:var(--white)}
/* contact */
.portrait{left:52px;top:2536px;width:350px;height:346px;border-radius:10px;background:linear-gradient(135deg,#e8edf0,#9aa6ad 55%,#2c3135);box-shadow:0 3px 6px rgba(0,0,0,.2)}
.form-head{font-size:28px;font-weight:700}
.field{border-bottom:1px solid var(--line);font-size:20px;font-style:italic;color:#c8c8c8;padding-left:10px;padding-bottom:8px}
.consent{left:611px;top:3226px;display:flex;align-items:center;gap:12px;font-size:15px}
.box{width:22px;height:22px;border:1px solid var(--line)}
/* footer */
.site-footer{left:0;top:3415px;width:1200px;height:407px;background:var(--sky)}
.foot-links{left:53px;top:3494px;font-size:20px;line-height:44.5px}
.foot-title{left:423px;top:3443px;font-size:20px;font-weight:700}
.foot-item{left:434px;font-size:21px;display:flex;align-items:center;gap:14px}
.map{left:798px;top:3484px;width:348px;height:179px;background:linear-gradient(135deg,#eef0ec,#dde6d8 60%,#f2dc9b)}
</style>
</head>
<body>

<header class="abs site-header">
  <div class="abs brand"><span class="brand-square"></span>PFLEGEPLATZ JOB</div>
  <nav class="abs main-nav"><span>STARTSEITE</span><span>ÜBER UNS</span><span>WIR BIETEN</span><span>REFERENZEN</span><span>KONTAKT</span></nav>
  <span class="abs social" style="left:1080px" aria-label="Social-Media-Link 1"></span>
  <span class="abs social" style="left:1124px" aria-label="Social-Media-Link 2"></span>
</header>

<section class="abs hero">
</section>
<h1 class="abs hero-title">Willkommen bei<br>PFLEGEPLATZ-JOB.de</h1>
<p class="abs hero-sub">Dein nächster Karriereschritt<br>im Pflegeberuf!</p>
<a class="abs btn btn-solid" style="left:49px;top:457px;width:166px;height:47px">Angebot</a>
<div class="abs video">
  <div class="abs video-chip"></div>
  <div class="abs video-name">PFLEGEPLATZ JOB</div>
  <div class="abs video-bar"><div class="abs video-track"></div></div>
</div>

<div class="abs rule" style="left:52px;top:810px;width:164px"></div>
<h2 class="abs section-title" style="left:52px;top:828px">Was darfst Du von<br><span class="accent">PFLEGEPLATZ-JOB.de</span> erwarten?</h2>

<div class="abs feature" style="left:144px;top:958px">
  <svg width="66" height="62" viewBox="0 0 66 62" fill="none" stroke="#29a9e1" stroke-width="3"><ellipse cx="33" cy="34" rx="24" ry="18"/><path d="M18 50v8M46 50v8M20 20l-4-10 10 6M57 32h5"/><circle cx="44" cy="30" r="2" fill="#29a9e1"/></svg>
  100% kostenfrei</div>
<div class="abs feature" style="left:423px;top:958px">
  <svg width="70" height="56" viewBox="0 0 70 56" fill="none" stroke="#29a9e1" stroke-width="3"><path d="M2 12l14-8 16 8 10-4 26 8M68 16L50 34M4 14l14 16 16 16 8-4 8 2 8-10M26 28l12-10 12 8"/></svg>
  Zugriff auf mehr Stellen</div>
<div class="abs feature" style="left:703px;top:958px">
  <svg width="52" height="62" viewBox="0 0 52 62" fill="none" stroke="#29a9e1" stroke-width="3"><path d="M4 2h30l14 14v44H4z M34 2v14h14"/><circle cx="26" cy="40" r="6"/><path d="M22 46l-2 10 6-4 6 4-2-10"/></svg>
  Alle Versprechungen im Arbeitsvertrag</div>
<div class="abs feature feature-note" style="left:144px;top:1278px">Dein neuer Arbeitgeber hält nicht was er verspricht? Keine Sorge, wir werden für Dich sofort wieder aktiv und bieten Dir schnell neue Möglichkeiten an - ohne dass Du erneut Bewerbungen versenden musst! Ein Anruf oder eine Email genügt!</div>
<div class="abs feature" style="left:423px;top:1278px">
  <svg width="58" height="62" viewBox="0 0 58 62" fill="none" stroke="#29a9e1" stroke-width="3"><path d="M29 2l26 10v18c0 16-12 26-26 30C15 56 3 46 3 30V12z"/><path d="M22 24a7 7 0 1 1 10 6c-3 2-3 4-3 7"/><circle cx="29" cy="44" r="1.5" fill="#29a9e1"/></svg>
  Anonymität</div>
<div class="abs feature" style="left:703px;top:1278px">
  <svg width="70" height="62" viewBox="0 0 70 62" fill="none" stroke="#29a9e1" stroke-width="3"><rect x="2" y="14" width="56" height="40" rx="6"/><path d="M20 14V6h20v8M2 30h30"/><circle cx="52" cy="44" r="14" fill="#fff"/><path d="M52 36v8l6 4"/></svg>
  Keine Zeitarbeit</div>

<svg class="abs" style="left:1134px;top:984px" width="16" height="40" viewBox="0 0 16 40" fill="none" stroke="#9c3a8d" stroke-width="2"><path d="M8 40V2M2 9l6-7 6 7"/></svg>
<div class="abs fab" style="top:1044px;background:#8a8a8a" aria-label="Telefon">
  <svg width="28" height="28" viewBox="0 0 24 24" fill="#fff"><path d="M6.6 10.8a15.1 15.1 0 0 0 6.6 6.6l2.2-2.2a1 1 0 0 1 1-.25 11.4 11.4 0 0 0 3.6.57 1 1 0 0 1 1 1V20a1 1 0 0 1-1 1A17 17 0 0 1 3 4a1 1 0 0 1 1-1h3.5a1 1 0 0 1 1 1c0 1.25.2 2.45.57 3.57a1 1 0 0 1-.25 1z"/></svg></div>
<div class="abs fab" style="top:1115px;background:var(--plum)" aria-label="E-Mail">
  <svg width="30" height="22" viewBox="0 0 30 22" fill="none" stroke="#fff" stroke-width="2"><rect x="1" y="1" width="28" height="20"/><path d="M1 1l14 11L29 1"/></svg></div>
<div class="abs fab" style="top:1185px;background:#3cc65a" aria-label="Messenger"></div>

<section class="abs reviews"></section>
<div class="abs rule" style="left:52px;top:1756px;width:164px"></div>
<h2 class="abs section-title" style="left:52px;top:1773px">Bewerber haben folgendes bei uns erlebt<br>und schildern ihre Erfahrung</h2>
<a class="abs btn btn-solid" style="left:980px;top:1769px;width:166px;height:46px">Mehr sehen</a>

<article class="abs review" style="left:52px">Lorem ipsum dolor sit amet, consetetur sadipscing elitr, sed diam nonumy eirmod tempor invidunt ut labore et dolore magna aliquyam
  <div class="review-foot"><span>Max Mustermann</span><span class="stars">★★★★★</span></div></article>
<article class="abs review" style="left:426px">Lorem ipsum dolor sit amet, consetetur sadipscing elitr, sed diam nonumy eirmod tempor invidunt ut labore et dolore magna aliquyam
  <div class="review-foot"><span>Max Mustermann</span><span class="stars">★★★★<span class="off">★</span></span></div></article>
<article class="abs review" style="left:798px">Lorem ipsum dolor sit amet, consetetur sadipscing elitr, sed diam nonumy eirmod tempor invidunt ut labore et dolore magna aliquyam
  <div class="review-foot"><span>Max Mustermann</span><span class="stars">★★★★★</span></div></article>
<div class="abs avatar" style="left:158px" role="img" aria-label="Porträtfoto einer Bewerberin"></div>
<div class="abs avatar" style="left:528px" role="img" aria-label="Porträtfoto einer Bewerberin"></div>
<div class="abs avatar" style="left:903px" role="img" aria-label="Porträtfoto einer Bewerberin"></div>

<div class="abs rule" style="left:52px;top:2425px;width:164px"></div>
<h2 class="abs section-title" style="left:52px;top:2443px">Nimm ganz einfach<br>Kontakt zu uns auf:</h2>
<div class="abs portrait" role="img" aria-label="Foto eines lächelnden Beraters im Anzug vor einem Bürofenster"></div>

<h3 class="abs form-head" style="left:609px;top:2528px">Angaben</h3>
<div class="abs field" style="left:609px;top:2592px;width:259px">Vorname*</div>
<div class="abs field" style="left:887px;top:2592px;width:259px">Nachname*</div>
<div class="abs field" style="left:609px;top:2666px;width:537px">E-Mail*</div>
<h3 class="abs form-head" style="left:609px;top:2765px">Nachricht</h3>
<div class="abs field" style="left:609px;top:2812px;width:537px;height:118px;padding-left:14px">max. 500 Zeichen</div>
<h3 class="abs form-head" style="left:609px;top:2981px">Upload Lebenslauf</h3>
<div class="abs" style="left:609px;top:3062px;width:537px;border-top:1px solid var(--line)"></div>
<a class="abs btn btn-outline" style="left:609px;top:3079px;width:165px;height:46px">Durchsuchen</a>
<a class="abs btn btn-outline" style="left:795px;top:3079px;width:165px;height:46px">Upload</a>
<label class="abs consent"><span class="box"></span>Ich habe die Datenschutzbestimmungen zur Kenntniss genommen. *</label>
<a class="abs btn btn-solid" style="left:982px;top:3257px;width:164px;height:46px">Senden</a>

<footer class="abs site-footer"></footer>
<nav class="abs foot-links"><div>Jobs</div><div>Impressum</div><div>Allgemeine Geschäftsbedingungen</div><div>Datenschutzerklärung</div></nav>
<div class="abs foot-title">Pflegeplatz Job</div>
<div class="abs foot-item" style="top:3497px">
  <svg width="20" height="26" viewBox="0 0 20 26" fill="#777"><path d="M10 0a10 10 0 0 0-10 10c0 7 10 16 10 16s10-9 10-16A10 10 0 0 0 10 0zm0 14a4 4 0 1 1 0-8 4 4 0 0 1 0 8z"/></svg>Lindenhof-Allee 12</div>
<div class="abs foot-item" style="left:463px;top:3545px">79100 Talheim</div>
<div class="abs foot-item" style="top:3584px">
  <svg width="22" height="16" viewBox="0 0 22 16" fill="#777"><path d="M0 0h22v16H0z"/><path d="M1 1l10 8 10-8" stroke="#7ecbea" stroke-width="1.5" fill="none"/></svg>Email:&nbsp;<u>info@pflegeplatz-job.de</u></div>
<div class="abs foot-item" style="top:3633px">
  <svg width="20" height="20" viewBox="0 0 24 24" fill="#777"><path d="M6.6 10.8a15.1 15.1 0 0 0 6.6 6.6l2.2-2.2a1 1 0 0 1 1-.25 11.4 11.4 0 0 0 3.6.57 1 1 0 0 1 1 1V20a1 1 0 0 1-1 1A17 17 0 0 1 3 4a1 1 0 0 1 1-1h3.5a1 1 0 0 1 1 1c0 1.25.2 2.45.57 3.57a1 1 0 0 1-.25 1z"/></svg>Phone: +49 170 5550123</div>
<div class="abs map" role="img" aria-label="Stadtplan mit Standortmarkierung des Büros"></div>

</body>
</html>
```